TalkHarbor - Language Coaching Services

Sleek, innovative, trendy design for Language Coaching business.

TalkHarbor is a new UK based company that provides Language Coaching services. We offer highly personalized on-line and face to face language courses. We also impart learning techniques workshops based on the latest neuroscience research for second-language acquisition.

Target Market(s)

See attached info

Industry/Entity Type

Consulting

Contact Information for Business Card

TalkHarbor
DaniaKV@talkharbor.co.uk
TalkHarbor.co.uk
London, UK

Font styles to use
Sans Serif

```html
<!DOCTYPE html>
<html lang="en">
<head>
<meta charset="utf-8">
<title>TalkHarbor Business Card</title>
<link href="https://fonts.googleapis.com/css2?family=Montserrat:wght@400;700&family=Open+Sans:wght@400;600&display=swap" rel="stylesheet">
<style>
  :root {
    --bg: #2b2d30;
    --blue-bright: #1bb4ea;
    --blue-mid: #0b8cc9;
    --blue-deep: #0b5f8f;
    --band: #0d6ea3;
    --band-dark: #0a5887;
    --paper: #f7f7f7;
    --ink-blue: #0c5d8e;
    --ink-grey: #9a9a9a;
    --white: #ffffff;
  }
  * { margin: 0; padding: 0; box-sizing: border-box; }
  html, body { width: 1200px; height: 892px; overflow: hidden; background: var(--bg); }
  .stage { position: relative; width: 1200px; height: 892px; }

  .card {
    position: absolute;
    left: 250px;
    width: 700px;
    height: 400px;
    overflow: hidden;
    box-shadow: 0 14px 30px rgba(0,0,0,0.45);
  }
  .card-front {
    top: 26px;
    background: radial-gradient(ellipse at 52% 48%, var(--blue-bright) 0%, var(--blue-mid) 40%, var(--blue-deep) 100%);
    display: flex; align-items: center; justify-content: center;
  }
  .front-wordmark {
    font-family: "Montserrat", sans-serif;
    font-weight: 700;
    font-size: 44px;
    letter-spacing: 3px;
    color: var(--white);
  }

  .card-back { top: 466px; background: var(--paper); }
  .back-band { position: absolute; inset: 0; }
  .back-wordmark {
    position: absolute; right: 34px; top: 34px;
    font-family: "Montserrat", sans-serif;
    font-weight: 400;
    font-size: 40px;
    letter-spacing: 2px;
    color: var(--blue-mid);
  }
  .holder { position: absolute; left: 50px; top: 150px; }
  .holder-name {
    font-family: "Montserrat", sans-serif; font-weight: 700;
    font-size: 22px; color: var(--ink-blue); letter-spacing: 0.5px;
  }
  .holder-title {
    font-family: "Open Sans", sans-serif; font-size: 15px;
    color: var(--ink-grey); letter-spacing: 1px; margin-top: 2px;
  }
  .contacts {
    position: absolute; left: 50px; bottom: 30px; list-style: none;
    font-family: "Open Sans", sans-serif; font-size: 19px; color: var(--white);
  }
  .contacts li { display: flex; align-items: center; gap: 12px; line-height: 28px; }
  .contacts svg { width: 18px; height: 18px; flex: none; }
</style>
</head>
<body>
<div class="stage">
  <section class="card card-front" aria-label="Business card front">
    <span class="front-wordmark">TALKHARBOR</span>
  </section>

  <section class="card card-back" aria-label="Business card back">
    <svg class="back-band" width="700" height="400" viewBox="0 0 700 400">
      <polygon points="0,268 700,150 700,400 0,400" fill="var(--band)"/>
      <polygon points="0,362 700,240 700,400 0,400" fill="var(--band-dark)" opacity="0.35"/>
      <circle cx="580" cy="178" r="76" fill="var(--white)" stroke="var(--blue-mid)" stroke-width="9"/>
    </svg>
    <div class="back-wordmark">TALKHARBOR</div>
    <div class="holder">
      <div class="holder-name">MAYA LORNE</div>
      <div class="holder-title">PRESIDENT</div>
    </div>
    <ul class="contacts">
      <li>
        <svg viewBox="0 0 18 18"><rect x="4" y="1" width="10" height="16" rx="2" fill="none" stroke="#fff" stroke-width="1.8"/><circle cx="9" cy="14" r="1" fill="#fff"/></svg>
        555 0142 7788
      </li>
      <li>
        <svg viewBox="0 0 18 18"><rect x="1" y="4" width="16" height="11" fill="#fff"/><polyline points="1,4 9,10 17,4" fill="none" stroke="var(--band)" stroke-width="1.5"/></svg>
        info@talkharbor.co.uk
      </li>
      <li>
        <svg viewBox="0 0 18 18"><circle cx="9" cy="9" r="7.5" fill="#fff"/><path d="M9 1.5v15M1.5 9h15" stroke="var(--band)" stroke-width="1.2"/></svg>
        TalkHarbor.co.uk
      </li>
    </ul>
  </section>
</div>
</body>
</html>
```